CopperWanderer Stretching and Strength

We need a application design for a our first IOS application. the goal of the application is to categorize stretching and strength routines for triathlon.

We would like to see designs that use the color orange.

The design of the application should be compliant with the last version of the IOS Mobile.

For this first design we need the folowing pages:

1- Sign up
2- Log in
3- Home
4- View Exercises
5- Do it
6- Profile

The description of each page is in the attached document.

We need a logo design for the application. The logo should express that mission of the application that is for stretch and strength training for Triathlon.

We will use https://pellavokit.example to develop the application, if you have any experience of the limitation that this technology have it will be a plus.

If you have any question please feel free to contact us.

Reason: We will extend the deadline to be sure that we select the best design from all of you. we will take the final decision next Tuesday.

Target Market(s)

The market for my aplicación is the Running a Triathlon world.

Logo Text

CopperWanderer

Font styles to use
Serif

Colors
f37122
ffffff
dcdcdc

Requirements
Must have
• In some future we will add more features in the menu. We should considere it for the design.
• The designs should include all the screens in the power point.

```html
<!DOCTYPE html>
<html lang="en">
<head>
<meta charset="utf-8">
<title>Strength Exercise – CopperWanderer</title>
<link href="https://fonts.googleapis.com/css2?family=Roboto:wght@400;500&display=swap" rel="stylesheet">
<style>
  :root {
    --page-bg: #d6e3ef;
    --orange: #f37122;
    --white: #ffffff;
    --list-bg: #eeeeee;
    --text-dark: #2a2a2a;
    --text-body: #666666;
    --tag-flex: #22b8e0;
    --tag-leg: #cf6fd6;
    --tag-pain: #7650e6;
    --tag-shoulder: #e6b53c;
  }
  * { box-sizing: border-box; margin: 0; padding: 0; }
  html, body { width: 1200px; height: 1200px; overflow: hidden; }
  body {
    background: var(--page-bg);
    font-family: "Roboto", sans-serif;
    display: flex;
    justify-content: center;
  }
  .screen {
    width: 672px;
    height: 1200px;
    background: var(--list-bg);
    overflow: hidden;
    position: relative;
  }
  .status-bar {
    height: 51px;
    background: var(--orange);
    color: var(--white);
    font-size: 20px;
    display: flex;
    align-items: center;
    justify-content: space-between;
    padding: 0 10px;
  }
  .status-left, .status-right { display: flex; align-items: center; gap: 8px; width: 200px; }
  .status-right { justify-content: flex-end; }
  .signal { display: flex; gap: 2px; }
  .signal span { width: 9px; height: 9px; border-radius: 50%; border: 1.5px solid var(--white); }
  .signal span.on { background: var(--white); }
  .battery { width: 38px; height: 16px; border: 1.5px solid var(--white); border-radius: 4px; padding: 2px; position: relative; }
  .battery::before { content: ""; display: block; width: 100%; height: 100%; background: var(--white); border-radius: 1px; }
  .battery::after { content: ""; position: absolute; right: -5px; top: 4px; width: 3px; height: 6px; background: var(--white); border-radius: 0 2px 2px 0; }
  .app-header {
    height: 69px;
    background: var(--orange);
    color: var(--white);
    display: flex;
    align-items: center;
    justify-content: space-between;
    padding: 0 16px;
  }
  .app-title { font-size: 28px; font-weight: 500; letter-spacing: 0.2px; }
  .search-bar {
    height: 56px;
    background: var(--white);
    display: flex;
    align-items: center;
    gap: 12px;
    padding: 0 20px;
    color: #777;
    font-size: 21px;
  }
  .exercise-list { padding: 15px 16px 0; display: flex; flex-direction: column; gap: 9px; }
  .exercise-card {
    background: var(--white);
    height: 173px;
    display: flex;
    padding: 20px 13px;
    gap: 20px;
    box-shadow: 0 1px 3px rgba(0,0,0,0.12);
  }
  .exercise-thumb { width: 97px; height: 93px; flex: none; }
  .exercise-info { flex: 1; }
  .exercise-title { font-size: 22px; font-weight: 400; color: var(--text-dark); line-height: 26px; margin-top: -4px; }
  .tags { display: flex; gap: 8px; margin: 4px 0 10px; }
  .tag {
    height: 17px; padding: 0 15px; border-radius: 9px;
    font-size: 11px; color: var(--white); line-height: 17px;
  }
  .tag-flex { background: var(--tag-flex); }
  .tag-leg { background: var(--tag-leg); }
  .tag-pain { background: var(--tag-pain); }
  .tag-shoulder { background: var(--tag-shoulder); }
  .exercise-desc { font-size: 17.5px; line-height: 27px; color: var(--text-body); }
  .exercise-meta { font-size: 16px; color: var(--text-body); margin-top: 2px; display: flex; gap: 29px; }
  .exercise-meta b { color: var(--orange); font-weight: 400; }
</style>
</head>
<body>
<main class="screen">
  <div class="status-bar">
    <div class="status-left">
      <div class="signal"><span class="on"></span><span class="on"></span><span class="on"></span><span></span><span></span></div>
      <span>NOVA</span>
    </div>
    <div class="status-time">4:21 PM</div>
    <div class="status-right">
      <span>100%</span>
      <div class="battery"></div>
    </div>
  </div>

  <header class="app-header">
    <svg width="32" height="22" viewBox="0 0 32 22" stroke="#fff" stroke-width="2.6"><path d="M0 2h32M0 11h32M0 20h32"/></svg>
    <h1 class="app-title">STRENGTH EXERCISE</h1>
    <svg width="28" height="28" viewBox="0 0 28 28" fill="#fff"><path d="M1 2h26l-10 12v12l-6-4v-8z"/></svg>
  </header>

  <div class="search-bar">
    <svg width="22" height="22" viewBox="0 0 22 22" fill="none" stroke="#333" stroke-width="2"><circle cx="9" cy="9" r="7"/><path d="M14 14l6 6"/></svg>
    <span>Search here...</span>
  </div>

  <section class="exercise-list">
    <article class="exercise-card">
      <div class="exercise-thumb" role="img" aria-label="Group of people doing outdoor lunge stretches in a park" style="background:linear-gradient(160deg,#c9d6b0,#5f7a45 60%,#3d4a3a)"></div>
      <div class="exercise-info">
        <h2 class="exercise-title">Lorem ipsum dolor sit amet</h2>
        <div class="tags"><span class="tag tag-flex">Flexibility</span><span class="tag tag-leg">Leg</span><span class="tag tag-pain">Pain Relief</span></div>
        <p class="exercise-desc">Lorem ipsum dolor sit amet, consectetur adipiscing elit. Etiam vitae eros efficitur...</p>
        <p class="exercise-meta"><span><b>Time:</b> 5:32 min</span><span><b>Level:</b> Moderate</span></p>
      </div>
    </article>

    <article class="exercise-card">
      <div class="exercise-thumb" role="img" aria-label="Woman holding a plank on a wooden floor" style="background:linear-gradient(180deg,#f1ece8,#e4d6cf 55%,#b06a45)"></div>
      <div class="exercise-info">
        <h2 class="exercise-title">Lorem ipsum dolor sit amet</h2>
        <div class="tags"><span class="tag tag-flex">Flexibility</span><span class="tag tag-leg">Leg</span><span class="tag tag-shoulder">Shoulder</span></div>
        <p class="exercise-desc">Lorem ipsum dolor sit amet, consectetur adipiscing elit. Etiam vitae eros efficitur...</p>
        <p class="exercise-meta"><span><b>Time:</b> 4:25 min</span><span><b>Level:</b> Easy</span></p>
      </div>
    </article>

    <article class="exercise-card">
      <div class="exercise-thumb" role="img" aria-label="Person in a forward-folding floor stretch" style="background:linear-gradient(180deg,#f2f2f2,#dcdcdc 60%,#c9c9c9)"></div>
      <div class="exercise-info">
        <h2 class="exercise-title">Lorem ipsum dolor sit amet</h2>
        <div class="tags"><span class="tag tag-flex">Flexibility</span><span class="tag tag-pain">Pain Relief</span></div>
        <p class="exercise-desc">Lorem ipsum dolor sit amet, consectetur adipiscing elit. Etiam vitae eros efficitur...</p>
        <p class="exercise-meta"><span><b>Time:</b> 3:10 min</span><span><b>Level:</b> Moderate</span></p>
      </div>
    </article>

    <article class="exercise-card">
      <div class="exercise-thumb" role="img" aria-label="Woman doing a seated hamstring stretch on a blue mat" style="background:linear-gradient(180deg,#ffffff,#f1f1f1 60%,#5aa3d8)"></div>
      <div class="exercise-info">
        <h2 class="exercise-title">Lorem ipsum dolor sit amet</h2>
        <div class="tags"><span class="tag tag-leg">Leg</span><span class="tag tag-pain">Pain Relief</span></div>
        <p class="exercise-desc">Lorem ipsum dolor sit amet, consectetur adipiscing elit. Etiam vitae eros efficitur...</p>
        <p class="exercise-meta"><span><b>Time:</b> 4:00 min</span><span><b>Level:</b> Moderate</span></p>
      </div>
    </article>

    <article class="exercise-card">
      <div class="exercise-thumb" role="img" aria-label="Class doing side plank poses on yoga mats" style="background:linear-gradient(180deg,#e9d3cc,#c98b86 55%,#5a6a8c)"></div>
      <div class="exercise-info">
        <h2 class="exercise-title">Lorem ipsum dolor sit amet</h2>
        <div class="tags"><span class="tag tag-pain">Pain Relief</span></div>
        <p class="exercise-desc">Lorem ipsum dolor sit amet, consectetur adipiscing elit. Etiam vitae eros efficitur...</p>
        <p class="exercise-meta"><span><b>Time:</b> 5:09 min</span><span><b>Level:</b> Easy</span></p>
      </div>
    </article>

    <article class="exercise-card">
      <div class="exercise-thumb" role="img" aria-label="Runners on an outdoor path" style="background:linear-gradient(180deg,#b8cde0,#7f8f6a 55%,#4a4a4a)"></div>
      <div class="exercise-info">
        <h2 class="exercise-title">Lorem ipsum dolor sit amet</h2>
        <div class="tags"><span class="tag tag-flex">Flexibility</span><span class="tag tag-leg">Leg</span></div>
        <p class="exercise-desc">Lorem ipsum dolor sit amet, consectetur adipiscing elit. Etiam vitae eros efficitur...</p>
        <p class="exercise-meta"><span><b>Time:</b> 4:40 min</span><span><b>Level:</b> Easy</span></p>
      </div>
    </article>
  </section>
</main>
</body>
</html>
```